Las Vegas Tour guide needs website of future for physical and selfguided assets

Neon Drifters is the parent site to my Las Vegas tour operation. Within this is a physical walking tour called Whispers and the Racket, the site traffic driver where I tell history with a paranormal twist. The legacy site can be seen at spookyroutewalks.com.
The Neon Drifters app has self guided tours called Desert Hop Trail/Whispers and The Racket Retold/Calloway Row Stroll. Rivano is a 3rd party tour company I have partnered with to sale self-guided tours with a scavenger hunt theme.
I like black and pink and pistachio green colors however am flexible in theme. Colors should follow Vegas 50-60s aesthetics. The “Greetings From Silver Gulch Marker” should not be considered as design inspiration. 95% of traffic is on mobile. Final design should be easy to understand guided versus self-guided option. Show cross promotion links for digital assets/physical tour. Rivano content tbd by end of week 9 Aug 2021
sites i like
nationalspiritstrolls.com
heronsandshades.com
oldportphantomtrips.net
Updates

Needs a book now at top, or floating like lorvantrips. Less busy and stay away from using photos. I have included more websites for inspiration. I would like a mashup of the two sites eerieechoplace and lorvantrips. I am unsure what some of your designs would look like on a mobile screen. Please screenshot that. https://eerieechoplace.com/ https://www.lorvantrips.com/ https://k7vrx.com/ https://bqspecters.com/ https://bluefinjaunts.com/tours/new-york-city/shades-of-pellham-corner/

Family member hospitalized need extra time to review

Target Market(s)

Tourist 25+

Industry/Entity Type

Travel. Tour guide.

Coding

Coded - Design and coding required

Number of Pages Required

5+ page

Font styles to use
Serif

Colors
00AB8E
00BBA5
67D7C9
C6EFE9
E9F9F6
59FF00
82FF00
B8FF75
E3FFCB
F4FFEA
EB3D1F
EC4F4E
F09395
F8D3D4
FCEDEE
E54698
E96AAD
F1A4CE
F9D9EA
FCEFF6

Requirements
Must have
• Cross promotion between physical tour and digital
Nice to have
• sliver button like ads as breaks between tour info
Should not have
• "Greetings from Silver Gulch Marker". no photos. no animation.

```html
<!DOCTYPE html>
<html lang="en">
<head>
<meta charset="utf-8">
<title>Whispers and the Racket Las Vegas Walking Tour</title>
<link href="https://fonts.googleapis.com/css2?family=Playfair+Display:wght@700;800&family=Lora:wght@400;500;600;700&display=swap" rel="stylesheet">
<style>
  :root {
    --ink: #1c1c1c;
    --muted: #5f5f5f;
    --pink: #e54698;
    --pink-soft: #f1a4ce;
    --pink-pale: #f9d9ea;
    --pink-mist: #fcefF6;
    --pistachio: #b8ff75;
    --pistachio-pale: #e3ffcb;
    --pistachio-mist: #f4ffea;
    --teal: #00ab8e;
    --teal-soft: #67d7c9;
    --teal-pale: #c6efe9;
    --coral: #ec4f4e;
    --footer: #1c1c1c;
    --white: #ffffff;
  }
  * { margin: 0; padding: 0; box-sizing: border-box; }
  html, body { width: 999px; height: 1200px; overflow: hidden; background: var(--white); }
  body { font-family: "Lora", serif; color: var(--ink); position: relative; }

  .hero-backdrop {
    position: absolute; left: 0; top: 0; width: 999px; height: 690px;
    background:
      linear-gradient(to bottom, rgba(255,255,255,0) 72%, #ffffff 100%),
      linear-gradient(to bottom, var(--pink-pale) 0%, var(--pink-mist) 38%, var(--pistachio-mist) 60%, var(--pistachio-pale) 80%, var(--teal-pale) 92%);
  }
  .brand {
    position: absolute; left: 95px; top: 60px;
    display: flex; align-items: center; gap: 9px;
    font-family: "Lora", serif; font-weight: 700; font-size: 17px; color: var(--ink);
  }
  .brand-dot { width: 18px; height: 18px; border-radius: 50%; background: var(--pink); }
  .menu-toggle { position: absolute; left: 887px; top: 63px; width: 19px; height: 15px; }

  .hero-title {
    position: absolute; left: 0; top: 200px; width: 990px;
    text-align: center; font-family: "Playfair Display", serif;
    font-weight: 800; font-size: 38px; line-height: 43px;
    text-transform: uppercase; color: var(--ink); letter-spacing: 0.5px;
  }
  .book-now {
    position: absolute; left: 421px; top: 303px; width: 157px; height: 48px;
    border-radius: 24px; background: var(--pink);
    display: flex; align-items: center; justify-content: center;
    font-family: "Lora", serif; font-weight: 700; font-size: 15px; letter-spacing: 0.5px;
    color: var(--white); text-decoration: none;
  }
  .tagline {
    position: absolute; left: 206px; top: 410px; width: 586px; height: 66px;
    background: rgba(103, 215, 201, 0.75);
    display: flex; align-items: center; justify-content: center; text-align: center;
    font-family: "Lora", serif; font-weight: 700; font-size: 14px; line-height: 21.5px;
    text-transform: uppercase; letter-spacing: 0.3px;
  }

  .highlights { position: absolute; left: 0; top: 551px; width: 999px; }
  .highlight { position: absolute; width: 259px; text-align: center; }
  .highlight-art { width: 259px; height: 259px; border-radius: 50%; }
  .highlight p {
    width: 226px; margin: 16px auto 0;
    font-size: 12.5px; line-height: 18.6px; color: var(--muted);
  }
  .art-properties { background: radial-gradient(circle at 40% 35%, var(--pink-pale) 0%, var(--pink-soft) 100%); }
  .art-mob { background: radial-gradient(circle at 40% 35%, var(--pistachio-pale) 0%, var(--pistachio) 100%); }
  .art-street { background: radial-gradient(circle at 40% 35%, var(--teal-pale) 0%, var(--teal-soft) 100%); }

  .details { position: absolute; left: 91px; top: 942px; }
  .details h2 {
    font-family: "Playfair Display", serif; font-weight: 800;
    font-size: 29px; line-height: 34px; letter-spacing: 0.3px;
  }
  .detail-list { list-style: none; margin-top: 12px; width: 420px; }
  .detail-list li {
    position: relative; padding-left: 23px;
    font-size: 12.5px; line-height: 21.4px; color: var(--ink);
  }
  .detail-list svg { position: absolute; left: 2px; top: 5px; width: 11px; height: 11px; }

  .app-preview {
    position: absolute; left: 623px; top: 923px; width: 191px; height: 229px;
    border-radius: 26px 26px 0 0; border: 3px solid var(--pink-pale); border-bottom: none;
    background: linear-gradient(to bottom, var(--white) 0%, var(--pink-mist) 30%, var(--pistachio-mist) 55%, var(--white) 100%);
  }

  .site-footer {
    position: absolute; left: 0; top: 1152px; width: 999px; height: 48px;
    background: var(--footer); color: var(--white);
    display: flex; align-items: center; justify-content: center;
    font-size: 12px;
  }
</style>
</head>
<body>
  <div class="hero-backdrop" role="img" aria-label="Soft pink to pistachio backdrop for the tour introduction"></div>

  <div class="brand"><span class="brand-dot"></span>Neon Drifters</div>

  <svg class="menu-toggle" viewBox="0 0 19 15" aria-label="Menu">
    <rect y="0" width="19" height="3" fill="#1c1c1c"/>
    <rect y="6" width="19" height="3" fill="#1c1c1c"/>
    <rect y="12" width="19" height="3" fill="#1c1c1c"/>
  </svg>

  <h1 class="hero-title">Whispers and the Racket Las<br>Vegas Walking Tour</h1>
  <a class="book-now" href="#">BOOK NOW</a>

  <div class="tagline">Explore Downtown Las Vegas and hear the history<br>of Fremont Street with a paranormal twist!</div>

  <section class="highlights">
    <div class="highlight" style="left:92px">
      <div class="highlight-art art-properties" role="img" aria-label="Haunted properties on the tour"></div>
      <p>Visit 3 haunted Las Vegas properties and hear the real stories that made them as they are</p>
    </div>
    <div class="highlight" style="left:370px">
      <div class="highlight-art art-mob" role="img" aria-label="Mob history highlights"></div>
      <p>Highlights include the ghosts of mob bodyguards and stories from the Motel of Death!</p>
    </div>
    <div class="highlight" style="left:647px">
      <div class="highlight-art art-street" role="img" aria-label="Guided walk through Downtown"></div>
      <p>Explore historic Downtown Las Vegas with an experienced guide on Fremont Street</p>
    </div>
  </section>

  <section class="details">
    <h2>DETAILS!</h2>
    <ul class="detail-list">
      <li><svg viewBox="0 0 11 11"><circle cx="5.5" cy="5.5" r="5.5" fill="#00ab8e"/><path d="M3 5.7l1.7 1.7 3.3-3.4" stroke="#fff" stroke-width="1.4" fill="none"/></svg>45 Minute walking tour</li>
      <li><svg viewBox="0 0 11 11"><circle cx="5.5" cy="5.5" r="5.5" fill="#00ab8e"/><path d="M3 5.7l1.7 1.7 3.3-3.4" stroke="#fff" stroke-width="1.4" fill="none"/></svg>Tour route less than one mile on accessible roads and sidewalks</li>
      <li><svg viewBox="0 0 11 11"><circle cx="5.5" cy="5.5" r="5.5" fill="#00ab8e"/><path d="M3 5.7l1.7 1.7 3.3-3.4" stroke="#fff" stroke-width="1.4" fill="none"/></svg>Rain or shine we almost always operate!</li>
      <li><svg viewBox="0 0 11 11"><circle cx="5.5" cy="5.5" r="5.5" fill="#00ab8e"/><path d="M3 5.7l1.7 1.7 3.3-3.4" stroke="#fff" stroke-width="1.4" fill="none"/></svg>Whispers and The Racket Retold Self Guided Tour also on Neon Drifters App!</li>
    </ul>
  </section>

  <div class="app-preview" role="img" aria-label="Phone showing the Neon Drifters app listing"></div>

  <footer class="site-footer">© Copyrights 2021 Company name | All Rights reserved</footer>
</body>
</html>
```